Wordpress Website - for cutting edge Artificial Intelligence company

We need a wordpress web site for our company Varlomex.

Objective:
- To promote our software products to potential customers (e.g. large corporations)
- To promote our software products to potential partners (e.g. software makers who want to bundle our software inside their products)
- To promote our company to potential Investors (venture capital funds, angel investors, etc.)

Sample content and proposed structure can be found in the attached file.
Company logo is also attached.

The Plover logo should only be used in the section relating to the Plover Product (e.g. Plover Text & Plover Speech)

Target Market(s)

Core Target Market:
- Large corporations (e.g. Major Banks, Retailers & Pharmaceutical companies) who could buy our software

Industry/Entity Type

Software

Coding

Coded - Design and coding required

Font styles to use
Sans Serif

Colors
ffffff
ec1f27
000000
757575
dfdfdf
9bcb3c

Requirements
Must have
• Functionality:
• - Designed in Wordpress (using tools from wordpress.org, not hosted on wordpress.com)
• - Must have a user friendly CMS module for us to make updates easily
• - Must be designed to look great across different devices
• - Must be designed to look great in English and Chinese (as well as other future languages).

```html
<!DOCTYPE html>
<html lang="en">
<head>
<meta charset="utf-8">
<title>Varlomex — Plover</title>
<link href="https://fonts.googleapis.com/css2?family=Open+Sans:wght@400;600;700&display=swap" rel="stylesheet">
<style>
:root{
  --red:#ec1f27;
  --black:#000000;
  --nav:#2b2b2b;
  --caption:#2f2f2f;
  --grey:#757575;
  --light:#dfdfdf;
  --white:#ffffff;
  --heading:#4a4a4a;
  --blue:#1594d6;
  --bottom:#161616;
}
*{margin:0;padding:0;box-sizing:border-box}
html,body{width:1200px;height:2267px;overflow:hidden;background:var(--white)}
body{position:relative;font-family:"Open Sans",Arial,sans-serif;color:var(--heading)}
.abs{position:absolute}

/* header */
.brand{left:100px;top:26px;font-size:44px;font-weight:700;color:var(--red);letter-spacing:2px;line-height:44px}
.search{left:671px;top:32px;width:257px;height:31px;border:1px solid #cfcfcf;font-size:12px;color:#8a8a8a;padding:6px 12px}
.search svg{position:absolute;right:9px;top:8px}
.phone-icon{left:952px;top:26px;width:39px;height:37px;background:var(--red);border-radius:3px}
.phone-icon svg{position:absolute;left:10px;top:9px}
.call{left:1006px;top:25px;font-size:12px;color:#555;line-height:20px}
.call .num{color:var(--red);font-size:13px}

.navbar{left:0;top:94px;width:1200px;height:42px;background:var(--nav)}
.nav-item{top:13px;font-size:13px;font-weight:700;color:var(--white);text-transform:uppercase}
.lang{left:997px;top:10px;width:102px;height:24px;background:#1c1c1c;font-size:9px;color:var(--white);padding:5px 0 0 32px}
.lang .flag{position:absolute;left:10px;top:7px;width:15px;height:10px;background:#3b4b8f}
.lang svg{position:absolute;right:9px;top:8px}

/* hero */
.hero{left:0;top:136px;width:1200px;height:549px;background:linear-gradient(90deg,#5a5450 0%,#8c847e 30%,#b9b3ab 55%,#d8d3c4 75%,#cfc9a8 100%)}
.hero-shade{left:0;top:136px;width:1200px;height:549px;background:rgba(0,0,0,.12)}
.hero-title{left:0;top:332px;width:1200px;text-align:center;font-size:45px;font-weight:700;color:var(--white);letter-spacing:.5px}
.hero-sub{left:0;top:394px;width:1200px;text-align:center;font-size:21px;font-weight:700;color:var(--white)}
.btn{top:452px;width:158px;height:41px;background:var(--blue);color:var(--white);font-size:13px;font-weight:700;text-align:center;line-height:41px;text-transform:uppercase}

/* sections */
.section-title{left:0;width:1200px;text-align:center;font-size:30px;font-weight:700;color:var(--heading);text-transform:uppercase}
.card{width:315px;height:277px}
.card .photo{width:315px;height:204px}
.card .caption{position:absolute;left:0;top:204px;width:315px;height:73px;background:var(--caption);color:var(--white);font-size:14px;font-weight:700;line-height:23px;padding:13px 20px 0;text-transform:uppercase}

.partner{width:300px;text-align:center}
.avatar{width:118px;height:118px;border-radius:50%;margin:0 auto;background:radial-gradient(circle at 50% 40%,#cfcfcf,#8d8d8d)}
.partner .name{margin-top:30px;font-size:13px;font-weight:700;color:#444;text-transform:uppercase}
.partner .role{margin-top:4px;font-size:13px;color:var(--grey)}
.partner .quote{position:relative;margin-top:16px;font-size:13px;line-height:25px;color:#555;padding:0 25px}
.qmark{position:absolute;font-size:30px;color:#bbb;font-family:Georgia,serif;line-height:30px}

/* footer */
.footer{left:0;top:1907px;width:1200px;height:308px;background:var(--black)}
.f-head{font-size:15px;font-weight:700;color:var(--white);text-transform:uppercase}
.f-link{font-size:12px;color:#d8d8d8}
.social{top:2019px;width:28px;height:28px;border-radius:50%;background:#8c8c8c}
.f-brand{left:842px;top:2094px;font-size:44px;font-weight:700;color:var(--red);letter-spacing:2px}
.bottom{left:0;top:2215px;width:1200px;height:52px;background:var(--bottom);color:#cfcfcf;font-size:12px;text-align:center;line-height:52px}
.bottom span{margin:0 14px}
</style>
</head>
<body>

<header>
  <div class="abs brand">VARLOMEX</div>
  <div class="abs search">Search :
    <svg width="12" height="12" viewBox="0 0 12 12"><circle cx="5" cy="5" r="4" fill="none" stroke="#999" stroke-width="1.3"/><line x1="8" y1="8" x2="11" y2="11" stroke="#999" stroke-width="1.3"/></svg>
  </div>
  <div class="abs phone-icon">
    <svg width="19" height="19" viewBox="0 0 24 24"><path d="M6.6 10.8c1.4 2.8 3.8 5.1 6.6 6.6l2.2-2.2c.3-.3.7-.4 1-.2 1.1.4 2.3.6 3.6.6.6 0 1 .4 1 1V20c0 .6-.4 1-1 1C10.6 21 3 13.4 3 4c0-.6.4-1 1-1h3.5c.6 0 1 .4 1 1 0 1.3.2 2.5.6 3.6.1.3 0 .7-.2 1z" fill="#fff"/></svg>
  </div>
  <div class="abs call">Call Us :<br><span class="num">( 5550 ) 412 087</span></div>

  <nav class="abs navbar">
    <span class="abs nav-item" style="left:100px">Natural Intelligence</span>
    <span class="abs nav-item" style="left:317px">Products</span>
    <span class="abs nav-item" style="left:449px">Services</span>
    <span class="abs nav-item" style="left:571px">Partners</span>
    <span class="abs nav-item" style="left:700px">Contact Us</span>
    <span class="abs nav-item" style="left:845px">About Us</span>
    <div class="abs lang"><span class="flag"></span>ENGLISH
      <svg width="8" height="6" viewBox="0 0 8 6"><path d="M1 1l3 3 3-3" fill="none" stroke="#fff" stroke-width="1.2"/></svg>
    </div>
  </nav>
</header>

<section>
  <div class="abs hero" role="img" aria-label="Smiling man with glasses working on a laptop in a bright office"></div>
  <div class="abs hero-shade"></div>
  <h1 class="abs hero-title">PLOVER, BY VARLOMEX</h1>
  <p class="abs hero-sub">THE NEW STANDARD IN CONTACT CENTER CUSTOMER EXPERIENCE</p>
  <a class="abs btn" style="left:437px">Request a Demo</a>
  <a class="abs btn" style="left:607px">Contact Us</a>
</section>

<section>
  <h2 class="abs section-title" style="top:732px">Recent News</h2>

  <article class="abs card" style="left:100px;top:805px">
    <div class="photo" role="img" aria-label="Hands typing on a laptop on a wooden desk" style="background:linear-gradient(180deg,#d9c7a8,#b59d78)"></div>
    <div class="caption">Lorem Ipsum is simply dummy text of the printing</div>
  </article>
  <article class="abs card" style="left:444px;top:805px">
    <div class="photo" role="img" aria-label="Group of young people walking in the street, black and white" style="background:linear-gradient(180deg,#bdbdbd,#6e6e6e)"></div>
    <div class="caption">Lorem Ipsum is simply dummy text of the printing</div>
  </article>
  <article class="abs card" style="left:787px;top:805px">
    <div class="photo" role="img" aria-label="Businessman on a phone call with a laptop on a bench" style="background:linear-gradient(180deg,#4a4a52,#2e3040)"></div>
    <div class="caption">Lorem Ipsum is simply dummy text of the printing</div>
  </article>

  <article class="abs card" style="left:100px;top:1112px">
    <div class="photo" role="img" aria-label="Young man in a beanie looking at his phone outdoors" style="background:linear-gradient(90deg,#8a9bb0,#c9b98a)"></div>
    <div class="caption">Lorem Ipsum is simply dummy text of the printing</div>
  </article>
  <article class="abs card" style="left:444px;top:1112px">
    <div class="photo" role="img" aria-label="Woman using a laptop on a sofa" style="background:linear-gradient(180deg,#6d5f52,#4b4540)"></div>
    <div class="caption">Lorem Ipsum is simply dummy text of the printing</div>
  </article>
  <article class="abs card" style="left:787px;top:1112px">
    <div class="photo" role="img" aria-label="Hand holding a smartphone with colourful apps" style="background:linear-gradient(90deg,#3c4c55,#9fb7b5)"></div>
    <div class="caption">Lorem Ipsum is simply dummy text of the printing</div>
  </article>
</section>

<section>
  <h2 class="abs section-title" style="top:1448px">Varlomex Partners</h2>

  <div class="abs partner" style="left:110px;top:1535px">
    <div class="avatar" role="img" aria-label="Portrait of a partner in a suit"></div>
    <div class="name">Dorian Pell</div>
    <div class="role">Business man</div>
    <div class="quote"><span class="qmark" style="left:0;top:-6px">&ldquo;</span>Lorem Ipsum is simply dummy text of the printing and typesetting industry. Lorem Ipsum has been the industry's standard dummy text ever since the 1500s<span class="qmark" style="right:0;bottom:-14px">&rdquo;</span></div>
  </div>
  <div class="abs partner" style="left:451px;top:1535px">
    <div class="avatar" role="img" aria-label="Portrait of a partner in a suit and tie"></div>
    <div class="name">Dorian Pell</div>
    <div class="role">Business man</div>
    <div class="quote"><span class="qmark" style="left:0;top:-6px">&ldquo;</span>Lorem Ipsum is simply dummy text of the printing and typesetting industry. Lorem Ipsum has been the industry's standard dummy text ever since the 1500s<span class="qmark" style="right:0;bottom:-14px">&rdquo;</span></div>
  </div>
  <div class="abs partner" style="left:800px;top:1535px">
    <div class="avatar" role="img" aria-label="Portrait of a smiling partner"></div>
    <div class="name">Dorian Pell</div>
    <div class="role">Business man</div>
    <div class="quote"><span class="qmark" style="left:0;top:-6px">&ldquo;</span>Lorem Ipsum is simply dummy text of the printing and typesetting industry. Lorem Ipsum has been the industry's standard dummy text ever since the 1500s<span class="qmark" style="right:0;bottom:-14px">&rdquo;</span></div>
  </div>
</section>

<footer>
  <div class="abs footer"></div>

  <div class="abs f-head" style="left:100px;top:1951px">Natural Intelligence</div>
  <div class="abs f-link" style="left:101px;top:1988px">What is NI</div>
  <div class="abs f-link" style="left:101px;top:2014px">NI vs. AI</div>
  <div class="abs f-link" style="left:101px;top:2041px">The Future of NI</div>
  <div class="abs f-head" style="left:100px;top:2089px">Partners</div>
  <div class="abs f-link" style="left:101px;top:2124px">Find a Partner</div>
  <div class="abs f-link" style="left:101px;top:2151px">Become a Partner</div>

  <div class="abs f-head" style="left:399px;top:1951px">Products</div>
  <div class="abs f-link" style="left:401px;top:1988px">Plover - Text</div>
  <div class="abs f-link" style="left:401px;top:2014px">Plover - Voice</div>
  <div class="abs f-head" style="left:399px;top:2072px">Contact Us</div>
  <div class="abs f-link" style="left:401px;top:2107px">120 Street name, City name,</div>
  <div class="abs f-link" style="left:401px;top:2134px">Country name : 695666</div>

  <div class="abs f-head" style="left:630px;top:1951px">Services</div>
  <div class="abs f-link" style="left:632px;top:1988px">Implementation Services</div>
  <div class="abs f-link" style="left:632px;top:2014px">Business Consulting</div>
  <div class="abs f-head" style="left:630px;top:2072px">About Us</div>
  <div class="abs f-link" style="left:632px;top:2107px">Company</div>
  <div class="abs f-link" style="left:632px;top:2134px">Newsroom</div>
  <div class="abs f-link" style="left:632px;top:2160px">Careers</div>

  <div class="abs f-head" style="left:870px;top:1951px">Contact Us</div>
  <div class="abs f-link" style="left:872px;top:1988px">Connect with our social network</div>
  <span class="abs social" style="left:872px"></span>
  <span class="abs social" style="left:908px"></span>
  <span class="abs social" style="left:944px"></span>
  <span class="abs social" style="left:980px"></span>
  <span class="abs social" style="left:1016px"></span>
  <div class="abs f-brand">VARLOMEX</div>

  <div class="abs bottom">Copyright © 2016. Varlomex. All rights reserved.<span></span>Sitemap<span>/</span>Terms of Use<span>/</span>Privacy Policy</div>
</footer>

</body>
</html>
```